A new novel about the early days of The Quillmen needs a book cover design

The title of the book is LANTERN ROW NIGHTS
The cover should also include "a novel" and "by Milo Fastwick" Those can be together or separate.
The design element I'd like to incorporate is the iconic "Pier Lamps" photo of The Quillmen in 1960, which I've attached below. Since we're not sure if we can get the rights to the actual photo, it's probably best if the design merely references that photo, or distorts it in an interesting way. But it should be very clear that the book is about The Quillmen.
The novel is in many ways based on that photo and evokes the city of Hamburg in 1960, which was gritty, raw, and sexually charged (as were The Quillmen).
The tone of the novel is romantic, passionate, and very funny - but never broad and silly.

```html
<!DOCTYPE html>
<html lang="en">
<head>
<meta charset="utf-8">
<title>Lantern Row Nights – Cover and Wrap</title>
<link rel="stylesheet" href="https://fonts.googleapis.com/css2?family=Abril+Fatface&family=Oranienbaum&family=Alfa+Slab+One&display=swap">
<style>
  :root {
    --sky-lilac: #b3a6f2;
    --violet-bright: #5a3df0;
    --violet-mid: #8b78e8;
    --violet-deep: #2c1aa8;
    --violet-night: #1c1170;
    --ink: #060508;
    --stone: #a9a6ab;
    --stone-dark: #6f6b72;
    --paper: #ffffff;
    --author-violet: #4b2be0;
  }
  * { margin: 0; padding: 0; box-sizing: border-box; }
  html, body { width: 1200px; height: 1200px; overflow: hidden; background: var(--paper); }
  .canvas { position: relative; width: 1200px; height: 1200px; }

  .front-cover {
    position: absolute;
    width: 420px; height: 630px;
    overflow: hidden;
    transform-origin: top left;
  }
  .front-cover--single { left: 402px; top: 0; }
  .front-cover--wrap { left: 640px; top: 638px; transform: scale(0.8976); }

  .cover-art {
    position: absolute; inset: 0;
    background:
      radial-gradient(ellipse 38% 12% at 55% 14%, rgba(200,190,250,0.85), rgba(200,190,250,0) 100%),
      radial-gradient(ellipse 30% 10% at 20% 30%, rgba(190,178,246,0.8), rgba(190,178,246,0) 100%),
      radial-gradient(ellipse 14% 36% at 27% 30%, var(--violet-deep), rgba(44,26,168,0) 100%),
      radial-gradient(ellipse 70% 14% at 60% 40%, var(--violet-night), rgba(28,17,112,0) 100%),
      radial-gradient(ellipse 60% 10% at 50% 60%, var(--ink), rgba(6,5,8,0) 100%),
      linear-gradient(180deg,
        var(--violet-bright) 0%, var(--violet-mid) 8%, var(--sky-lilac) 20%, var(--violet-mid) 28%,
        var(--violet-deep) 38%, var(--violet-bright) 44%, var(--violet-deep) 50%,
        var(--ink) 56%, var(--ink) 67%, var(--stone-dark) 70%, var(--stone) 78%,
        var(--stone-dark) 84%, var(--stone) 92%, var(--stone-dark) 100%);
  }
  .author-name {
    position: absolute; top: 14px; left: 0; right: 0;
    text-align: center;
    font-family: "Alfa Slab One", serif;
    font-size: 34px; color: var(--paper);
    -webkit-text-stroke: 1.5px var(--ink);
    paint-order: stroke fill;
  }
  .book-title {
    position: absolute; top: 444px; left: 0; right: 0;
    text-align: center;
    font-family: "Abril Fatface", serif;
    font-size: 64px; line-height: 1;
    color: var(--ink);
    -webkit-text-stroke: 3px var(--paper);
    paint-order: stroke fill;
    white-space: nowrap;
  }
  .book-tagline {
    position: absolute; top: 596px; left: 0; right: 0;
    text-align: center;
    font-family: "Alfa Slab One", serif;
    font-size: 18px; color: var(--ink);
  }

  .back-cover {
    position: absolute; left: 217px; top: 638px;
    width: 376px; height: 562px;
    background: var(--ink); overflow: hidden;
  }
  .back-art {
    position: absolute; left: 0; top: 0; width: 376px; height: 190px;
    background:
      radial-gradient(ellipse 30% 14% at 55% 12%, rgba(200,190,250,0.85), rgba(200,190,250,0) 100%),
      radial-gradient(ellipse 12% 50% at 32% 40%, var(--violet-deep), rgba(44,26,168,0) 100%),
      linear-gradient(180deg, var(--violet-mid) 0%, var(--sky-lilac) 18%, var(--violet-mid) 32%,
        var(--violet-bright) 48%, var(--violet-deep) 62%, var(--ink) 80%, var(--ink) 100%);
  }
  .back-blurb {
    position: absolute; left: 29px; top: 208px; width: 306px;
    font-family: "Oranienbaum", serif;
    font-size: 11px; line-height: 15.6px;
    color: var(--paper); text-align: justify;
    hyphens: auto;
  }
  .back-blurb p + p { margin-top: 15px; }
  .isbn-box {
    position: absolute; left: 214px; top: 455px;
    width: 149px; height: 81px; background: var(--paper);
  }

  .spine {
    position: absolute; left: 596px; top: 638px; width: 42px; height: 562px;
  }
  .spine-title, .spine-author {
    position: absolute; left: 0; width: 42px;
    writing-mode: vertical-rl;
    display: flex; align-items: center;
    font-family: "Abril Fatface", serif;
    white-space: nowrap;
  }
  .spine-title { top: 18px; font-size: 26px; color: var(--ink); }
  .spine-author { top: 424px; font-size: 15px; color: var(--author-violet); }
</style>
</head>
<body>
<main class="canvas">

  <section class="front-cover front-cover--single">
    <div class="cover-art" role="img" aria-label="Stylised violet posterised scene of a 1960 Hamburg street at dusk with a church spire and lamp-lit facades; five young Quillmen in black leather with guitars and a snare drum seated on a bench on the cobbled ground"></div>
    <p class="author-name">Milo Fastwick</p>
    <h1 class="book-title">Lantern Row<br>Nights</h1>
    <p class="book-tagline">A novel</p>
  </section>

  <section class="back-cover">
    <div class="back-art" role="img" aria-label="Violet Hamburg street with church spire, the five Quillmen shown as black silhouettes"></div>
    <div class="back-blurb">
      <p>Lorem ipsum dolor sit amet, consectetur adipiscing elit, sed do eiusmod tempor incididunt ut labore et dolore magna aliqua. Ut enim ad minim veniam, quis nostrud exercitation ullamco laboris nisi ut aliquip ex ea commodo consequat. Duis aute irure dolor in reprehenderit in voluptate velit esse cillum dolore eu fugiat nulla pariatur. Excepteur sint occaecat cupidatat non proident, sunt in culpa qui officia deserunt mollit anim id est laborum.</p>
      <p>Lorem ipsum dolor sit amet, consectetur adipiscing elit, sed do eiusmod tempor incididunt ut labore et dolore magna aliqua. Ut enim ad minim veniam, quis nostrud exercitation ullamco laboris nisi ut aliquip ex ea commodo consequat. Duis aute irure dolor in reprehenderit in voluptate velit esse cillum dolore eu fugiat nulla pariatur. Excepteur sint occaecat cupidatat non proident, sunt in culpa qui officia deserunt mollit anim id est laborum ge5t64w576e45 hbdfhsrtrthfghfdber bdf jkytj.</p>
    </div>
    <div class="isbn-box"></div>
  </section>

  <section class="spine">
    <p class="spine-title">Lantern Row Nights</p>
    <p class="spine-author">Milo Fastwick</p>
  </section>

  <section class="front-cover front-cover--wrap">
    <div class="cover-art" role="img" aria-label="Stylised violet posterised scene of a 1960 Hamburg street at dusk with a church spire and lamp-lit facades; five young Quillmen in black leather with guitars and a snare drum seated on a bench on the cobbled ground"></div>
    <p class="author-name">Milo Fastwick</p>
    <h2 class="book-title">Lantern Row<br>Nights</h2>
    <p class="book-tagline">A novel</p>
  </section>

</main>
</body>
</html>
```